Halvik - consultancy website

I need a new design for my webpage/presence [to be functioning with Wordpress - I have a programmer to set it up but not the design idea].
My company is Halvik - a consultancy firm focused on growth management for Swedish SME's primarily;. We call it Leadership toolkit for firms on the rise, kind of a doctor helping small become big. Contentwise, its a simple frontpage + 3-4 subpages with content re company/myself/focus etc. The new site should communicate a fresh, trustworthy take yet simple and functional on all devices [i.e. think UI compatible for mobile/tablet]. Current building parts/form elements are
a) existing logo and text elements
b) existing pictures
c) the yellowish color
colours and new ideas on pictures/positioning are welcome. I prefer a 'full width page' solution with centralised text elements but that's all up to you to suggest. Current site is a quickfix made by myself - now I'm moving it to a new platform so want to take the opportunity to make it
Nothing superspecial as it is a 2-man show; on the other hand I still want to have a modern & fresh reflection of my brand in digital environments. Help me out!
www.halvik-demo.se
Best
Lina Bergqvist

```html
<!DOCTYPE html>
<html lang="en">
<head>
<meta charset="utf-8">
<title>Halvik</title>
<link rel="stylesheet" href="https://fonts.googleapis.com/css2?family=Arimo:ital,wght@0,400;0,700;1,400&family=Noto+Serif&display=swap">
<style>
:root{
  --accent:#f0a030;
  --ink:#1a1a1a;
  --text:#444;
  --muted:#888;
  --white:#fff;
  --footer:#1e1e1e;
  --footer-base:#121212;
  --line:#3a3a3a;
  --fb:#3b5898;
  --tw:#3eaee2;
  --gp:#dd4b39;
  --red:#d9302a;
}
*{margin:0;padding:0;box-sizing:border-box}
html,body{width:750px;height:1200px;overflow:hidden}
body{position:relative;font-family:"Arimo",Arial,sans-serif;color:var(--text);background:var(--white)}
.abs{position:absolute}

/* hero */
.hero{left:0;top:0;width:750px;height:384px;background:radial-gradient(ellipse at 50% 45%,#d9a25e 0%,#c38a48 45%,#9a6a35 100%)}
.header{left:0;top:0;width:750px;height:72px;background:rgba(245,235,222,.55)}
.logo{left:62px;top:12px;font-family:"Noto Serif",Georgia,serif;font-size:30px;color:var(--ink);line-height:1}
.tagline{left:63px;top:44px;font-family:"Noto Serif",Georgia,serif;font-size:8.5px;color:var(--ink)}
.nav{left:432px;top:30px;display:flex;gap:21px;font-size:8.5px;font-weight:700;color:var(--ink)}
.nav .active{color:#a0661e;position:relative}
.nav .active::after{content:"";position:absolute;left:-11px;right:-11px;top:16px;height:3px;background:var(--accent)}
.caption{right:71px;text-align:right;font-size:16px;font-weight:700;color:var(--white);background:rgba(60,40,25,.55);padding:1px 5px;line-height:20px}
.cap1{top:275px}.cap2{top:298px}
.hero-btn{left:616px;top:326px;width:65px;height:21px;background:#000;color:var(--white);font-size:8.5px;text-align:center;line-height:21px}
.dots{left:706px;top:343px;display:flex;gap:4px}
.dots span{width:6px;height:6px;border-radius:50%;border:1px solid #222}
.dots span:first-child{background:#222}

/* about */
.about-title{left:0;width:750px;top:410px;text-align:center;font-size:16px;font-weight:700;color:var(--ink)}
.about-text{left:64px;width:622px;top:443px;text-align:center;font-size:7px;line-height:14px;color:var(--text)}
.about-btn{left:337px;top:515px;width:75px;height:22px;background:var(--accent);color:var(--white);font-size:8px;text-align:center;line-height:22px}

/* testimonials */
.testimonials{left:0;top:581px;width:750px;height:225px;background:linear-gradient(180deg,#2a2526 0%,#3a302b 55%,#231f20 100%)}
.testi-title{left:0;width:750px;top:603px;text-align:center;font-size:16px;font-weight:700;color:var(--white)}
.avatar{left:343px;top:637px;width:66px;height:66px;border-radius:50%;background:radial-gradient(circle,#8d8d8d,#4a4a4a);border:3px solid rgba(0,0,0,.35)}
.quote{font-family:Georgia,serif;font-size:46px;color:#8a8a8a;line-height:1;font-weight:700}
.q-open{left:128px;top:693px}
.q-close{left:599px;top:746px}
.testi-text{left:150px;width:450px;top:718px;text-align:center;font-style:italic;font-size:7px;line-height:13px;color:#e6e6e6}
.testi-name{left:0;width:750px;top:767px;text-align:center;font-size:7px;color:var(--white)}
.testi-name small{font-size:5.5px;color:#ccc}
.arrow{top:683px}

/* news */
.news-title{left:60px;top:834px;font-size:15px;font-weight:700;color:var(--ink)}
.news-nav{top:836px;width:15px;height:14px}
.news-prev{left:654px;background:var(--accent)}
.news-next{left:672px;background:var(--ink)}
.card-img{width:98px;height:80px;top:883px}
.card-body{top:882px;width:94px}
.card-body h3{font-size:7px;font-weight:400;line-height:11px;color:var(--ink)}
.card-meta{font-size:5.5px;color:var(--text);margin-top:3px;padding-bottom:3px;border-bottom:1px solid #ccc}
.card-body p{font-size:6px;line-height:9px;color:#666;margin-top:5px}
.card-link{font-size:5.5px;color:var(--red);margin-top:5px;display:flex;align-items:center;gap:3px}

/* footer */
.footer{left:0;top:1025px;width:750px;height:144px;background:var(--footer)}
.foot-base{left:0;top:1169px;width:750px;height:31px;background:var(--footer-base)}
.foot-h{top:1050px;font-size:9px;color:var(--white)}
.divider{top:1051px;width:1px;height:99px;background:var(--line)}
.social{top:1079px;width:45px;height:58px;color:var(--white);font-size:7.5px;text-align:center}
.social i{display:block;width:25px;height:25px;border-radius:50%;background:rgba(0,0,0,.18);margin:7px auto 8px}
.fb{left:62px;background:var(--fb)}
.tw{left:111px;background:var(--tw)}
.gp{left:161px;background:var(--gp)}
.mail-text{left:334px;top:1076px;width:150px;font-size:7px;line-height:12px;color:#999}
.mail-input{left:334px;top:1107px;width:126px;height:18px;background:var(--white);font-size:6px;color:#aaa;padding-left:10px;line-height:18px}
.mail-btn{left:460px;top:1107px;width:19px;height:18px;background:var(--accent)}
.privacy{left:334px;top:1130px;font-size:6.5px;color:#777}
.menu{left:607px;top:1077px;font-size:7px;line-height:13.5px;color:var(--white);list-style:none}
.copyright{left:0;width:750px;top:1181px;text-align:center;font-size:6.5px;color:#777}
</style>
</head>
<body>

<section class="abs hero" role="img" aria-label="Photo: a tired person face down at a messy breakfast table, seen from above"></section>
<header class="abs header"></header>
<div class="abs logo">Halvik.</div>
<div class="abs tagline">Leadership toolkit for firms on the rise</div>
<nav class="abs nav"><span class="active">Home</span><span>About Us</span><span>Services</span><span>Gallery</span><span>Contact Us</span></nav>
<div class="abs caption cap1">Got you act together?</div>
<div class="abs caption cap2">Congratulations</div>
<div class="abs hero-btn">Read More</div>
<div class="abs dots"><span></span><span></span><span></span></div>

<h2 class="abs about-title">About Halvik</h2>
<p class="abs about-text">Lorem ipsum dolor sit amet, consectetur adipiscing elit. Fusce tristique ultricies dui et porta. Sed luctus mauris at dictum auctor. Ut sit amet eleifend tortor, vel fermentum ante. Sed luctus tellus eget tortor mollis, in ullamcorper erat facilisis. Pellentesque bibendum nec nisi ut consectetur. Mauris et elit id est luctus dapibus laoreet scelerisque arcu. Nam varius tincidunt enim quis ultricies. Morbi eleifend, dui faucibus gravida pellentesque, dui lectus tristique ante, et tempor metus ante ut mauris. Quisque feugiat massa ut nisi iaculis pulvinar. Ut euismod mauris enim, ac ultrices massa dignissim ac.</p>
<div class="abs about-btn">View More</div>

<section class="abs testimonials" role="img" aria-label="Photo: city skyline and bridge at night"></section>
<h2 class="abs testi-title">Testimonials</h2>
<div class="abs avatar" role="img" aria-label="Portrait photo of the client"></div>
<div class="abs quote q-open">&ldquo;</div>
<div class="abs quote q-close">&rdquo;</div>
<p class="abs testi-text">Mauris interdum velit leo, ac porta leo vehicula sed. Maecenas iaculis cursus magna. Vestibulum molestie, urna vel lobortis dictum, lacus nibh varius elit, ac tristique sapien dui sit amet diam. Phasellus hendrerit, augue vitae tristique rhoncus, felis urna blandit mauris, vel egestas ex tellus quis leo. Morbi at lacus in</p>
<div class="abs testi-name"><b>Mattias,</b> <small>Lorme ipsum</small></div>
<svg class="abs arrow" style="left:20px" width="14" height="28" viewBox="0 0 14 28"><path d="M13 1 1 14l12 13" fill="none" stroke="#fff" stroke-width="1"/></svg>
<svg class="abs arrow" style="left:718px" width="14" height="28" viewBox="0 0 14 28"><path d="M1 1l12 13L1 27" fill="none" stroke="#fff" stroke-width="1"/></svg>

<h2 class="abs news-title">Latest News</h2>
<svg class="abs news-nav news-prev" viewBox="0 0 15 14"><path d="M8.5 4.5 6 7l2.5 2.5" fill="none" stroke="#fff"/></svg>
<svg class="abs news-nav news-next" viewBox="0 0 15 14"><path d="M6.5 4.5 9 7l-2.5 2.5" fill="none" stroke="#fff"/></svg>

<div class="abs card-img" style="left:62px;background:linear-gradient(135deg,#d8d4cc,#8a8580)" role="img" aria-label="Photo: two businessmen looking at a tablet"></div>
<article class="abs card-body" style="left:168px">
  <h3>Lorem ipsum dolor sit amet, consectetur</h3>
  <div class="card-meta">15/05/2016 &nbsp;- &nbsp;&nbsp;Friday</div>
  <p>Mauris interdum velit leo, ac porta leo vehicula sed. Maece-nas iaculis</p>
  <div class="card-link">Read More <svg width="7" height="7" viewBox="0 0 7 7"><circle cx="3.5" cy="3.5" r="3" fill="none" stroke="#d9302a" stroke-width=".8"/><path d="M2 3.5h3M3.8 2.3 5 3.5 3.8 4.7" fill="none" stroke="#d9302a" stroke-width=".8"/></svg></div>
</article>

<div class="abs card-img" style="left:273px;background:linear-gradient(135deg,#8fa6c4,#3d5478)" role="img" aria-label="Photo: business handshake over documents"></div>
<article class="abs card-body" style="left:379px">
  <h3>Lorem ipsum dolor sit amet, consectetur</h3>
  <div class="card-meta">15/05/2016 &nbsp;- &nbsp;&nbsp;Friday</div>
  <p>Mauris interdum velit leo, ac porta leo vehicula sed. Maece-nas iaculis</p>
  <div class="card-link">Read More <svg width="7" height="7" viewBox="0 0 7 7"><circle cx="3.5" cy="3.5" r="3" fill="none" stroke="#d9302a" stroke-width=".8"/><path d="M2 3.5h3M3.8 2.3 5 3.5 3.8 4.7" fill="none" stroke="#d9302a" stroke-width=".8"/></svg></div>
</article>

<div class="abs card-img" style="left:484px;background:linear-gradient(180deg,#e8e6dc,#8c8a80 70%,#4a4845)" role="img" aria-label="Photo: team silhouettes in a bright office meeting room"></div>
<article class="abs card-body" style="left:590px">
  <h3>Lorem ipsum dolor sit amet, consectetur</h3>
  <div class="card-meta">15/05/2016 &nbsp;- &nbsp;&nbsp;Friday</div>
  <p>Mauris interdum velit leo, ac porta leo vehicula sed. Maece-nas iaculis</p>
  <div class="card-link">Read More <svg width="7" height="7" viewBox="0 0 7 7"><circle cx="3.5" cy="3.5" r="3" fill="none" stroke="#d9302a" stroke-width=".8"/><path d="M2 3.5h3M3.8 2.3 5 3.5 3.8 4.7" fill="none" stroke="#d9302a" stroke-width=".8"/></svg></div>
</article>

<footer class="abs footer"></footer>
<h4 class="abs foot-h" style="left:61px">Let's Connect</h4>
<div class="abs social fb"><i></i>2598</div>
<div class="abs social tw"><i></i>4576</div>
<div class="abs social gp"><i></i>1269</div>
<div class="abs divider" style="left:273px"></div>
<h4 class="abs foot-h" style="left:334px">Mailing List</h4>
<p class="abs mail-text">Sign up for our mailing list to get latest updates and offers.</p>
<div class="abs mail-input">Email address</div>
<svg class="abs mail-btn" viewBox="0 0 19 18"><path d="M6.5 9 8.5 11 12.5 7" fill="none" stroke="#fff" stroke-width="1.4"/></svg>
<div class="abs privacy">We respect your privacy</div>
<div class="abs divider" style="left:546px"></div>
<h4 class="abs foot-h" style="left:607px">Menu</h4>
<ul class="abs menu"><li>Home</li><li>About Us</li><li>Services</li><li>Gallery</li><li>Contact Us</li></ul>
<div class="abs foot-base"></div>
<div class="abs copyright">© Copyrights 2015 All Rights Reserved</div>

</body>
</html>
```